Mobile friendly Website design

Client is a packaging equipment company that would like a clean, mobile friendly design. They want a different home page than what they have now. The home page should have the traditional sliders, content area, services are and a featured products area. Please provide an internal page design too.

Target Market(s)

Companies who use packaging equipment, shrink wrappers, heat sealers and carton erectors.

Industry/Entity Type

It Company

Number of Pages Required

2 page

Font styles to use
Serif
Sans Serif

Requirements
Must have
• Must have a clean, mobile friendly design.

```html
<!DOCTYPE html>
<html lang="en">
<head>
<meta charset="utf-8">
<title>Halverd Packaging</title>
<link href="https://fonts.googleapis.com/css2?family=Roboto:wght@300;400;500;700&family=Open+Sans:ital,wght@0,400;0,600;1,400&display=swap" rel="stylesheet">
<style>
:root{
  --red:#c21f2d;
  --red-dark:#a51723;
  --navy:#2c2769;
  --navy-dark:#231f57;
  --ink:#222;
  --body:#555;
  --muted:#888;
  --light:#f3f3f3;
  --line:#ddd;
  --bar:#1d1d1d;
  --white:#fff;
}
*{margin:0;padding:0;box-sizing:border-box}
html,body{width:1200px;height:2866px;overflow:hidden}
body{font-family:"Open Sans",Arial,sans-serif;color:var(--body);background:var(--white);position:relative}
.wrap{position:relative;width:1002px;margin:0 auto}
h2.section-title{font-family:"Roboto",Arial,sans-serif;font-weight:400;font-size:31px;text-align:center;color:var(--navy);letter-spacing:.3px}
.rule{width:92px;height:2px;background:var(--line);margin:14px auto 0}

/* header */
.site-header{height:124px}
.brand{position:absolute;left:0;top:30px;display:flex;align-items:center;gap:10px}
.brand-name{font-family:"Roboto",sans-serif;font-weight:700;font-size:36px;color:var(--red);line-height:1}
.brand-mark{width:16px;height:16px;background:var(--navy);border-radius:50%}
.header-contact{position:absolute;left:675px;top:36px;width:230px;font-size:13px;color:#666;line-height:25px;padding-left:48px;white-space:nowrap}
.header-contact svg{position:absolute;left:0;top:10px}
.social{position:absolute;right:0;top:48px;display:flex;gap:5px}
.social span{width:24px;height:24px;border-radius:50%;display:block}

/* nav */
.main-nav{height:52px;background:linear-gradient(var(--red),var(--red-dark));border-bottom:4px solid var(--navy)}
.main-nav ul{list-style:none;display:flex;height:48px;align-items:center}
.main-nav li{font-family:"Roboto",sans-serif;font-size:14px;color:var(--white);margin-right:48px;position:relative}
.main-nav li.active:after{content:"";position:absolute;left:50%;bottom:-18px;margin-left:-7px;border:7px solid transparent;border-bottom-color:var(--navy)}

/* hero */
.hero{height:493px;background:linear-gradient(100deg,#7e8a98 0%,#b7b2a8 40%,#d9752c 62%,#c9cdd2 85%,#9aa4ae 100%);position:relative}
.hero-caption{position:absolute;left:99px;top:174px;width:363px;height:170px;background:rgba(44,39,105,.88);padding:22px 20px}
.hero-caption h1{font-family:"Roboto",sans-serif;font-weight:500;color:var(--white);font-size:44px;line-height:46px;text-transform:uppercase}
.hero-caption h1 small{display:block;font-size:36px;font-weight:400}
.dots{display:flex;gap:8px;margin-top:14px}
.dots span{width:11px;height:11px;border-radius:50%;background:var(--white)}
.dots span.on{box-shadow:0 0 0 3px rgba(255,255,255,.5)}

/* welcome */
.welcome{height:292px;background:var(--light);padding-top:58px;text-align:center}
.welcome h2{font-family:"Roboto",sans-serif;font-weight:400;font-size:31px;color:var(--ink)}
.welcome h2 em{font-style:normal;color:var(--red)}
.welcome p{font-size:11.5px;line-height:22px;width:880px;margin:22px auto 0;color:#555}
.welcome p + p{margin-top:14px}

/* services */
.services{height:444px;padding-top:60px}
.service-grid{display:grid;grid-template-columns:repeat(4,1fr);margin-top:52px;text-align:center}
.service svg{height:72px}
.service h3{font-family:"Roboto",sans-serif;font-weight:400;font-size:17px;color:var(--navy);margin-top:18px}
.service p{font-size:11.5px;line-height:21px;width:210px;margin:10px auto 0;height:63px;overflow:hidden}
.btn-more{display:inline-block;margin-top:10px;border:1px solid #bbb;border-radius:3px;font-size:11px;padding:4px 14px;color:#444}

/* featured */
.featured{height:525px;background:linear-gradient(var(--red),#b51c2a);padding-top:50px;position:relative}
.featured h2.section-title{color:var(--white)}
.featured .rule{background:rgba(255,255,255,.5)}
.product-row{display:grid;grid-template-columns:repeat(4,234px);gap:22px;margin-top:32px}
.product{background:var(--white);border-radius:5px;height:321px;padding:14px 16px;text-align:center}
.product .shot{height:150px;background:linear-gradient(#eceef0,#c9ccd0);border-radius:3px}
.product h3{font-family:"Roboto",sans-serif;font-weight:400;font-size:15.5px;color:var(--ink);margin-top:20px;text-transform:uppercase;white-space:nowrap}
.product p{font-size:11.5px;line-height:19px;margin-top:6px;height:57px;overflow:hidden}
.stars{margin-top:8px;font-size:11px;letter-spacing:1px;color:#e5a313}
.stars i{font-style:normal;color:#ccc}
.slider-arrow{position:absolute;top:335px}

/* blog */
.blog{height:503px;padding-top:56px}
.blog h2.section-title{color:var(--ink)}
.post-row{display:grid;grid-template-columns:repeat(3,314px);gap:30px;margin-top:32px}
.post .thumb{height:164px}
.post h3{font-family:"Open Sans",sans-serif;font-weight:400;font-size:15px;color:#444;margin-top:20px}
.meta{font-size:11px;font-style:italic;color:#666;margin-top:14px;display:flex;gap:16px;align-items:center}
.meta span{display:flex;gap:6px;align-items:center}
.post p{font-size:11.5px;line-height:22px;margin-top:12px}

/* partners */
.partners{height:109px;background:var(--light);border-top:1px solid #e4e4e4}
.partners ul{list-style:none;display:flex;justify-content:space-between;align-items:center;height:109px;padding:0 0 0 10px}
.partners li{font-family:"Roboto",sans-serif;font-weight:700;font-size:22px;color:#333;display:flex;align-items:center;gap:8px}
.partners li i{width:20px;height:20px;display:block}

/* footer */
.site-footer{height:263px;background:var(--navy);color:#e9e8f3;padding-top:40px}
.footer-grid{display:grid;grid-template-columns:220px 295px 320px 1fr}
.footer-brand{padding-top:38px}
.footer-brand .brand-name{color:var(--white);font-size:32px}
.footer-social{display:flex;gap:6px;margin-top:24px;padding-left:20px}
.footer-social span{width:24px;height:24px;border:1.5px solid var(--white);border-radius:50%}
.site-footer h4{font-family:"Roboto",sans-serif;font-weight:400;font-size:17px;color:var(--white);margin-bottom:18px;white-space:nowrap}
.contact-list{list-style:none;font-size:13px;line-height:19px}
.contact-list li{position:relative;padding-left:30px;margin-bottom:14px}
.contact-list svg{position:absolute;left:0;top:2px}
.news p{font-size:11.5px;line-height:20px;width:270px}
.news .field{width:258px;height:40px;background:var(--white);margin-top:18px;font-size:11px;color:#666;padding:12px}
.news .subscribe{display:inline-block;background:var(--red);color:var(--white);font-size:12px;padding:12px 14px;margin-top:14px}
.quick{list-style:none;font-size:12.5px;line-height:24px;white-space:nowrap}
.quick li:before{content:"";display:inline-block;border:4px solid transparent;border-left:5px solid var(--white);margin-right:12px}
.copyright{height:61px;background:var(--bar);color:#ccc;font-size:12px;text-align:center;line-height:61px}
</style>
</head>
<body>

<header class="site-header">
  <div class="wrap">
    <div class="brand"><span class="brand-name">Halverd</span><span class="brand-mark"></span></div>
    <div class="header-contact">
      <svg width="26" height="30" viewBox="0 0 24 24" fill="#bbb"><path d="M6.6 10.8a15 15 0 006.6 6.6l2.2-2.2a1 1 0 011-.25 11.4 11.4 0 003.6.6 1 1 0 011 1V20a1 1 0 01-1 1A17 17 0 013 4a1 1 0 011-1h3.5a1 1 0 011 1c0 1.25.2 2.45.6 3.6a1 1 0 01-.25 1z"/></svg>
      sales@halverdco.com<br>Call Us : +(555) 210-4830
    </div>
    <div class="social"><span style="background:#3b5b9a"></span><span style="background:#38a7de"></span><span style="background:#d9362c"></span></div>
  </div>
</header>

<nav class="main-nav">
  <div class="wrap">
    <ul>
      <li class="active">HOME</li><li>ABOUT US</li><li>PACKAGING PRODUCTS</li><li>PACKAGING EQUIPMENT SPECIALS</li><li>SUPPORT</li><li>CONTACT US</li>
    </ul>
  </div>
</nav>

<section class="hero" role="img" aria-label="Orange industrial robot arm lifting a cardboard box on a packaging line">
  <div class="hero-caption">
    <h1>Packaging<small>Equipment Parts</small></h1>
    <div class="dots"><span class="on"></span><span></span><span></span><span></span></div>
  </div>
</section>

<section class="welcome">
  <h2>WELCOME TO <em>HALVERD PACKAGING</em></h2>
  <p>Halverd Packaging Equipment Company attributes its success in the packaging industry to its commitment to customer service. Our factory trained service technicians have over 100 years of combined experience. Halverd Packaging Equipment Company takes pride in providing an immediate response to your service needs. With our commitment to customer service Halverd Packaging has become the packaging leader in the Midwest for equipment sales and packaging supplies.</p>
  <p>Halverd Packaging's lineup of premier manufacturers are the best in the industry. Halverd Packaging Equipment Company continues to bring the latest in innovative packaging ideas to companies just like yours. Contact us today and "Get your packaging needs on the right track!"</p>
</section>

<section class="services">
  <div class="wrap">
    <h2 class="section-title">OUR SERVICES</h2>
    <div class="service-grid">
      <div class="service">
        <svg viewBox="0 0 80 72" width="80"><g fill="var(--navy)"><circle cx="48" cy="26" r="20"/><circle cx="24" cy="52" r="15"/></g><g fill="var(--white)"><circle cx="48" cy="26" r="8"/><circle cx="24" cy="52" r="6"/></g></svg>
        <h3>Training &amp; Installation</h3>
        <p>Halverd technicians have more than 100 years of combined experience servicing all types of packaging equipment.</p>
        <span class="btn-more">Learn More</span>
      </div>
      <div class="service">
        <svg viewBox="0 0 72 72" width="72"><g fill="var(--navy)"><path d="M10 62l34-34 6 6-34 34z"/><path d="M54 4a14 14 0 00-12 20l-4 4 6 6 4-4a14 14 0 0020-12l-8 4-6-6 4-8z"/><path d="M8 6l8 0 30 30-8 8-30-30z"/></g></svg>
        <h3>Machine Repair</h3>
        <p>Ongoing preventative maintenance programs are available and can be customized to meet your</p>
        <span class="btn-more">Learn More</span>
      </div>
      <div class="service">
        <svg viewBox="0 0 90 72" width="90"><g fill="none" stroke="var(--navy)" stroke-width="5"><circle cx="60" cy="22" r="16"/><circle cx="60" cy="22" r="5"/><path d="M8 62h74M14 62l40-34"/></g></svg>
        <h3>Parts Sales</h3>
        <p>Halverd takes pride in providing an immediate response to your parts needs. Our extensive inventory allows</p>
        <span class="btn-more">Learn More</span>
      </div>
      <div class="service">
        <svg viewBox="0 0 72 72" width="72"><g fill="var(--navy)"><path d="M14 10c6 0 12 12 10 18l-6 4c4 10 12 18 22 22l4-6c6-2 18 4 18 10l-8 8C28 64 6 42 6 18z"/><path d="M52 6a12 12 0 00-10 16L28 36l6 6 14-14a12 12 0 0016-10l-7 3-5-5 3-7z"/></g></svg>
        <h3>Competent Phone</h3>
        <p>Our technical staff is trained to provide answers to all your questions quickly and completely. From mechanical</p>
        <span class="btn-more">Learn More</span>
      </div>
    </div>
  </div>
</section>

<section class="featured">
  <svg class="slider-arrow" style="left:36px" width="26" height="60" viewBox="0 0 26 60"><path d="M24 2L3 30l21 28" fill="none" stroke="#fff" stroke-width="2"/></svg>
  <svg class="slider-arrow" style="right:36px" width="26" height="60" viewBox="0 0 26 60"><path d="M2 2l21 28L2 58" fill="none" stroke="#fff" stroke-width="2"/></svg>
  <div class="wrap">
    <h2 class="section-title">FEATURED PRODUCTS</h2>
    <div class="rule"></div>
    <div class="product-row">
      <div class="product">
        <div class="shot" role="img" aria-label="Horizontal wrap labeling machine on a steel stand"></div>
        <h3>LX350 Horizontal</h3>
        <p>The LX350 Horizontal Wrap Labeler is built to automatically apply pressure sensitive labels onto round products.</p>
        <div class="stars">★★★<i>★★</i></div>
      </div>
      <div class="product">
        <div class="shot" role="img" aria-label="Rolls of black resin ribbon"></div>
        <h3>R220 Resin Enhanced</h3>
        <p>R220 Resin enhanced wax ribbons are the most common general purpose bar code ribbon. Wax ribbons print well.</p>
        <div class="stars">★★★<i>★★</i></div>
      </div>
      <div class="product">
        <div class="shot" role="img" aria-label="Top labeling machine on a steel stand"></div>
        <h3>LX200 Top Labeler</h3>
        <p>The LX200 Top Labeler is built to automatically apply pressure sensitive labels onto the top or side of flat items.</p>
        <div class="stars">★★★<i>★★</i></div>
      </div>
      <div class="product">
        <div class="shot" role="img" aria-label="Colorful printed shrink film packages"></div>
        <h3>Durafilm Printed Shrink</h3>
        <p>There's never been a better way than with colorful printed shrink film like Durafilm Printed Shrink Film.</p>
        <div class="stars">★★★<i>★★</i></div>
      </div>
    </div>
  </div>
</section>

<section class="blog">
  <div class="wrap">
    <h2 class="section-title">LATEST BLOG</h2>
    <div class="rule"></div>
    <div class="post-row">
      <article class="post">
        <div class="thumb" role="img" aria-label="Stacked wooden pallets in a warehouse" style="background:linear-gradient(135deg,#6b5a44,#b39a72 55%,#4d4a48)"></div>
        <h3>Nemo enim ipsam voluptatem quia</h3>
        <div class="meta"><span>▦ March 25, 2016</span><span>▢ No comments</span></div>
        <p>Lorem ipsum dolor sit amet, consectetur adipiscing elit, sed do eiusmod tempor incididunt ut labore et dolore magna aliqua. Ut enim ad minim veniam,</p>
      </article>
      <article class="post">
        <div class="thumb" role="img" aria-label="Warehouse aisle with tall shelving and a forklift" style="background:linear-gradient(135deg,#8e8a86,#c7c1b6 50%,#6e6a68)"></div>
        <h3>Nemo enim ipsam voluptatem quia</h3>
        <div class="meta"><span>▦ March 25, 2016</span><span>▢ No comments</span></div>
        <p>Lorem ipsum dolor sit amet, consectetur adipiscing elit, sed do eiusmod tempor incididunt ut labore et dolore magna aliqua. Ut enim ad minim veniam,</p>
      </article>
      <article class="post">
        <div class="thumb" role="img" aria-label="Brick office building in winter" style="background:linear-gradient(#bfc4c8,#9b8a7c 55%,#d8d8d6)"></div>
        <h3>Nemo enim ipsam voluptatem quia</h3>
        <div class="meta"><span>▦ March 25, 2016</span><span>▢ No comments</span></div>
        <p>Lorem ipsum dolor sit amet, consectetur adipiscing elit, sed do eiusmod tempor incididunt ut labore et dolore magna aliqua. Ut enim ad minim veniam,</p>
      </article>
    </div>
  </div>
</section>

<section class="partners">
  <div class="wrap">
    <ul>
      <li><i style="background:var(--navy);border-radius:50%"></i>Norland</li>
      <li>Corvane</li>
      <li style="color:var(--navy)">Tessel Wrap</li>
      <li style="color:var(--red)">Brandel</li>
      <li style="color:#1f5fa8"><i style="background:#1f5fa8"></i>Kestrel</li>
    </ul>
  </div>
</section>

<footer class="site-footer">
  <div class="wrap footer-grid">
    <div class="footer-brand">
      <span class="brand-name">Halverd</span>
      <div class="footer-social"><span></span><span></span><span></span><span></span></div>
    </div>
    <div>
      <h4>CONTACT US</h4>
      <ul class="contact-list">
        <li><svg width="14" height="18" viewBox="0 0 14 18"><path d="M7 1a6 6 0 00-6 6c0 4.5 6 10 6 10s6-5.5 6-10a6 6 0 00-6-6z" fill="none" stroke="#fff" stroke-width="1.5"/><circle cx="7" cy="7" r="2" fill="#fff"/></svg>Fairmont, Kansas<br>2280 N Cedar Ridge Rd, Fairmont, KS<br>(555) 210-4831</li>
        <li><svg width="16" height="16" viewBox="0 0 24 24"><path d="M6.6 10.8a15 15 0 006.6 6.6l2.2-2.2a1 1 0 011-.25 11.4 11.4 0 003.6.6 1 1 0 011 1V20a1 1 0 01-1 1A17 17 0 013 4a1 1 0 011-1h3.5a1 1 0 011 1c0 1.25.2 2.45.6 3.6a1 1 0 01-.25 1z" fill="none" stroke="#fff" stroke-width="1.6"/></svg>Phone: (555) 210-4830</li>
        <li><svg width="18" height="14" viewBox="0 0 18 14"><rect x="1" y="1" width="16" height="12" fill="none" stroke="#fff" stroke-width="1.5"/><path d="M1 1l8 7 8-7" fill="none" stroke="#fff" stroke-width="1.5"/></svg>E-Mail: sales@halverdco.com</li>
      </ul>
    </div>
    <div class="news">
      <h4>SUBSCRIBE TO OUR NEWSLETTER</h4>
      <p>Excepteur sint occaecat cupidatat nicht proident, sunt in culpa qui nicht proident,</p>
      <div class="field">Enter Email</div>
      <span class="subscribe">SUBSCRIBE</span>
    </div>
    <div>
      <h4>QUICK LINKS</h4>
      <ul class="quick"><li>Home</li><li>About Us</li><li>Packaging Products</li><li>Packaging Equipment</li><li>Support</li><li>Contact Us</li></ul>
    </div>
  </div>
</footer>

<div class="copyright">Copyright © Halverd Packaging, Inc. 2016. All Rights Reserved.</div>

</body>
</html>
```